Timber Crest Construction Needs business card

Hey we are in need of business card designs. I have upload our logo as a guideline, but free feel to run with it or come up with something unique.
Pls have fun with it and be creative. the name says it all!
i will give some directions after i see a few entries..
Updates
Logo source file has been uploaded..
Hey because of the logo is so colourful already.
Can we have a few submissions with less colour.
Also we are looking for clever/hidden/descriptive business card.

```html
<!DOCTYPE html>
<html lang="en">
<head>
<meta charset="utf-8">
<title>Timber Crest Construction – Business Card</title>
<link href="https://fonts.googleapis.com/css2?family=Jost:wght@400;500;600&display=swap" rel="stylesheet">
<style>
  :root {
    --backdrop: #1f7a03;
    --card-dark: #000000;
    --card-light: #ffffff;
    --brand-grey: #858585;
    --ink: #1c1c1c;
    --accent-red: #e8202a;
    --block-grey: #3b3b3d;
    --block-mid: #6a6a6c;
  }
  * { margin: 0; padding: 0; box-sizing: border-box; }
  html, body { width: 1200px; height: 1200px; overflow: hidden; }
  body {
    background: var(--backdrop);
    position: relative;
    font-family: "Jost", "Futura", sans-serif;
  }
  .card {
    position: absolute;
    left: 212px;
    width: 800px;
    height: 445px;
  }
  .card--front { top: 130px; background: var(--card-dark); }
  .card--back { top: 641px; background: var(--card-light); }

  .wordmark {
    position: absolute;
    color: var(--brand-grey);
    font-weight: 600;
    text-align: center;
    line-height: 1;
  }
  .wordmark__name { display: block; letter-spacing: -0.5px; }
  .wordmark__sub { display: block; letter-spacing: 1px; }

  .card--front .wordmark {
    left: 0; right: 0; top: 240px;
  }
  .card--front .wordmark__name { font-size: 44px; }
  .card--front .wordmark__sub { font-size: 14px; margin-top: 4px; }

  .card--back .wordmark {
    left: 92px; top: 52px; width: 332px;
  }
  .card--back .wordmark__name { font-size: 42px; }
  .card--back .wordmark__sub { font-size: 14px; margin-top: 4px; }

  .holder {
    position: absolute;
    left: 87px; top: 184px;
    font-size: 15px;
    letter-spacing: 3.5px;
    color: var(--ink);
  }
  .holder__name { font-weight: 600; }
  .holder__sep { margin: 0 6px; }
  .holder__role { color: var(--accent-red); font-weight: 400; }

  .address {
    position: absolute;
    left: 87px; top: 236px;
    font-size: 13.5px;
    letter-spacing: 2.4px;
    line-height: 21px;
    color: var(--ink);
  }

  .contacts {
    position: absolute;
    left: 87px; top: 297px;
    list-style: none;
    font-size: 14px;
    letter-spacing: 2px;
    color: var(--ink);
  }
  .contacts li {
    display: flex;
    align-items: center;
    height: 25px;
  }
  .contacts svg {
    width: 15px; height: 15px;
    margin-right: 21px;
    fill: none;
    stroke: var(--accent-red);
    stroke-width: 1.4;
  }

  .feature-graphic {
    position: absolute;
    left: 446px; top: 148px;
    width: 354px; height: 297px;
    background: linear-gradient(160deg, var(--block-mid), var(--block-grey));
  }
</style>
</head>
<body>
  <section class="card card--front">
    <div class="wordmark">
      <span class="wordmark__name">TIMBER CREST</span>
      <span class="wordmark__sub">CONSTRUCTION</span>
    </div>
  </section>

  <section class="card card--back">
    <div class="wordmark">
      <span class="wordmark__name">TIMBER CREST</span>
      <span class="wordmark__sub">CONSTRUCTION</span>
    </div>

    <p class="holder">
      <span class="holder__name">MARTA KELLAN</span><span class="holder__sep">-</span><span class="holder__role">DIRECTOR</span>
    </p>

    <p class="address">SHOP 3, 212-218 HARBOUR<br>ROAD WESTFIELD NORTH</p>

    <ul class="contacts">
      <li>
        <svg viewBox="0 0 16 16"><path d="M2 6c0-2 3-3 6-3s6 1 6 3l-3 1-1-2H6L5 7z"/><rect x="3" y="8" width="10" height="6" rx="1"/><circle cx="8" cy="11" r="1.5"/></svg>
        9651 2740
      </li>
      <li>
        <svg viewBox="0 0 16 16"><rect x="4" y="2" width="8" height="4"/><rect x="2" y="6" width="12" height="6"/><rect x="4" y="10" width="8" height="4"/></svg>
        9651 2748
      </li>
      <li>
        <svg viewBox="0 0 16 16"><rect x="2" y="4" width="12" height="8"/><path d="M2 4l6 5 6-5"/></svg>
        marta@kellanbuild.com
      </li>
      <li>
        <svg viewBox="0 0 16 16"><circle cx="8" cy="8" r="6"/><ellipse cx="8" cy="8" rx="2.5" ry="6"/><path d="M2 8h12"/></svg>
        www.kellanbuild.com
      </li>
    </ul>

    <div class="feature-graphic" role="img" aria-label="Large decorative building graphic in the brand's multicolour tones"></div>
  </section>
</body>
</html>
```